Email signature required - I have a logo and similar design examples

I would like an email signature similar to the examples i have uploaded. My company is Pinemark and we are a sign company installing signs for real estate agents. i already have my logo design, i just need an email signature. I would like images similar to the samples i have attached. We are a company installing for sale signs at houses that are for sale. please see my website for further information.

These are my details i want on the signature:

Kind regards
Owen
Tel: 0333 4819265 Web: www.pinemark-example.co.uk Email: owen@pinemark-example.co.uk
Unit 14, Ashdale Road Industrial Estate
Thornvale
Westmoor
TV4 3QZ

Industry/Entity Type

Real Estate

Requirements
Must have
• graphic images like samples

```html
<!DOCTYPE html>
<html lang="en">
<head>
<meta charset="utf-8">
<title>Pinemark – Email Signature</title>
<link rel="stylesheet" href="https://fonts.googleapis.com/css2?family=Montserrat:wght@700&family=Roboto:wght@400&display=swap">
<style>
  :root {
    --brand-red: #c8193c;
    --brand-navy: #1f2160;
    --text-grey: #555659;
    --card-white: #ffffff;
    --page-bg: #ecebe8;
  }
  * { margin: 0; padding: 0; box-sizing: border-box; }
  html, body {
    width: 1200px;
    height: 530px;
    overflow: hidden;
    background: var(--page-bg);
  }
  .signature {
    position: absolute;
    left: 30px;
    top: 68px;
    width: 1042px;
    height: 360px;
    background: var(--card-white);
    transform: scale(1.094);
    transform-origin: top left;
    box-shadow: 0 2px 6px rgba(0,0,0,0.12);
    font-family: "Roboto", Arial, sans-serif;
  }
  .details {
    position: absolute;
    left: 48px;
    top: 0;
    width: 400px;
    height: 100%;
  }
  .brand {
    position: absolute;
    top: 46px;
    left: 0;
    display: flex;
    align-items: center;
    gap: 10px;
  }
  .brand-name {
    font-family: "Montserrat", Arial, sans-serif;
    font-weight: 700;
    font-size: 42px;
    color: var(--brand-red);
    letter-spacing: -0.5px;
  }
  .brand-mark {
    width: 16px;
    height: 16px;
    background: var(--brand-navy);
  }
  .person-name {
    position: absolute;
    top: 130px;
    left: 0;
    font-family: "Montserrat", Arial, sans-serif;
    font-weight: 700;
    font-size: 33px;
    color: var(--brand-red);
  }
  .address {
    position: absolute;
    top: 184px;
    left: 0;
    font-size: 17.5px;
    line-height: 25px;
    color: var(--text-grey);
    white-space: nowrap;
  }
  .contact {
    position: absolute;
    top: 249px;
    left: 0;
    font-size: 17.5px;
    line-height: 25px;
    border-collapse: collapse;
    white-space: nowrap;
  }
  .contact th {
    text-align: left;
    font-weight: 400;
    color: var(--brand-red);
    width: 67px;
    padding: 0;
  }
  .contact td {
    color: var(--text-grey);
    padding: 0;
  }
  .divider {
    position: absolute;
    top: 0;
    width: 4px;
    height: 100%;
    background: var(--brand-navy);
  }
  .divider--left { left: 450px; }
  .divider--right { left: 986px; }
  .gallery {
    position: absolute;
    left: 461px;
    top: 6px;
    width: 520px;
    height: 345px;
    display: grid;
    grid-template-columns: repeat(3, 1fr);
    grid-template-rows: repeat(2, 1fr);
    gap: 8px;
  }
  .photo { width: 100%; height: 100%; }
  .photo--brick-house { background: linear-gradient(160deg, #8fb6e0 0%, #c98b6a 45%, #b06a4c 70%, #b7c84a 100%); }
  .photo--terrace-a,
  .photo--terrace-b { background: linear-gradient(180deg, #6f91b9 0%, #a38a62 35%, #8c7452 75%, #5d5a50 100%); }
  .photo--agent-boards { background: linear-gradient(150deg, #d7c6a7 0%, #a4694c 45%, #e6e6ea 70%, #d9336b 100%); }
  .photo--front-door-a,
  .photo--front-door-b { background: linear-gradient(170deg, #7a4a3a 0%, #a2543f 40%, #c6d23a 65%, #3a3636 100%); }
  .social {
    position: absolute;
    left: 990px;
    top: 0;
    width: 52px;
    height: 100%;
    display: flex;
    flex-direction: column;
    align-items: center;
    padding-top: 20px;
    gap: 8px;
  }
  .social-item {
    display: flex;
    flex-direction: column;
    align-items: center;
    gap: 6px;
  }
  .social-dot {
    width: 20px;
    height: 20px;
    border-radius: 50%;
    background: var(--brand-red);
  }
  .social-handle {
    writing-mode: vertical-rl;
    font-size: 19px;
    color: var(--text-grey);
    letter-spacing: 0.5px;
  }
</style>
</head>
<body>
  <div class="signature">
    <section class="details">
      <div class="brand">
        <span class="brand-name">Pinemark</span>
        <span class="brand-mark" aria-hidden="true"></span>
      </div>
      <div class="person-name">Owen</div>
      <p class="address">Unit 14, Ashdale Road Industrial Estate<br>Thornvale, Westmoor, TV4 3QZ</p>
      <table class="contact">
        <tr><th>Tel:</th><td>0333 4819265</td></tr>
        <tr><th>Email:</th><td>owen@pinemark-example.co.uk</td></tr>
        <tr><th>Web:</th><td>www.pinemark-example.co.uk</td></tr>
      </table>
    </section>

    <div class="divider divider--left"></div>

    <section class="gallery">
      <div class="photo photo--brick-house" role="img" aria-label="Photo of a brick house with a green for sale board"></div>
      <div class="photo photo--terrace-a" role="img" aria-label="Photo of new-build terraced houses with agent boards"></div>
      <div class="photo photo--terrace-b" role="img" aria-label="Photo of new-build terraced houses with agent boards"></div>
      <div class="photo photo--agent-boards" role="img" aria-label="Photo of estate agent for sale and to let boards outside houses"></div>
      <div class="photo photo--front-door-a" role="img" aria-label="Photo of a brick house front door with a yellow for sale sign"></div>
      <div class="photo photo--front-door-b" role="img" aria-label="Photo of a brick house front door with a yellow for sale sign"></div>
    </section>

    <div class="divider divider--right"></div>

    <aside class="social">
      <div class="social-item">
        <span class="social-dot" aria-hidden="true"></span>
        <span class="social-handle">/Pinemark</span>
      </div>
      <div class="social-item">
        <span class="social-dot" aria-hidden="true"></span>
        <span class="social-handle">@Pinemark</span>
      </div>
    </aside>
  </div>
</body>
</html>
```